IT Management and Consulting company wants a design

The website should transfer an innovative, forward-oriented, optimistic, and serious image to my customer. Because we work in an agile, the design should transfer this approach.

The new color should make a serious, but not boring, impression for the business visitors of top-level companies.

The main focus topics are:
* IT strategy consulting
* Digital transformation
* IT quality management

The website should be in the English language.

The website should be created for WordPress. The existing website is http://www.vldn-consult.example (no WordPress) is provided by servplanet.de. A WordPress sandbox system exists.

Target Market(s)

Purchasing departments, IT decision makers from companies, project recruiting companies

Industry/Entity Type

IT-Provider, Telecommunication, Automotive

Number of Pages Required

4 page

Font styles to use
Serif
Sans Serif

Requirements
Must have
• Long-pager scrolling, a detail page for each portfolio topics, contact page, page about the company
Nice to have
• Parallax animation less is more, maybe a nice Hero Video Header, interessting 3D graph, Isometric graphs will bi nice, more clean than overloaded,
Should not have
• personal recruting page like in www.v-tek.com

```html
<!DOCTYPE html>
<html lang="en">
<head>
<meta charset="utf-8">
<title>Velden Consulting</title>
<link href="https://fonts.googleapis.com/css2?family=Lora:wght@700&family=Roboto:wght@400;500;700&family=Poppins:wght@400;500;600;700&display=swap" rel="stylesheet">
<style>
:root{
  --gold:#bb7f06;
  --gold-dark:#a06c04;
  --ink:#1b1b1b;
  --text:#6d6d6d;
  --paper:#f4f4f4;
  --white:#ffffff;
  --black:#000000;
}
*{box-sizing:border-box;margin:0;padding:0}
html,body{width:1200px;height:4131px;overflow:hidden}
body{position:relative;background:var(--white);font-family:'Roboto',Arial,sans-serif;color:var(--text)}
.abs{position:absolute}
.serif{font-family:'Lora',Georgia,serif;font-weight:700;color:var(--ink);text-transform:uppercase}
.btn{position:absolute;background:var(--gold);color:var(--white);font:700 13.5px 'Roboto',Arial,sans-serif;text-transform:uppercase;display:flex;align-items:center;justify-content:center;letter-spacing:.2px}
.copy{font-size:13.5px;line-height:21.4px;color:var(--text)}

/* header */
.site-header{position:absolute;left:0;top:0;width:1200px;height:106px;background:var(--white);border-top:4px solid var(--gold)}
.brand{position:absolute;left:146px;top:36px;font:500 27px 'Poppins',sans-serif;color:var(--gold);line-height:1}
.brand-mark{position:absolute;left:118px;top:22px;width:14px;height:14px;border:2px solid #b5b5b5;border-radius:50%}
.tagline{position:absolute;left:148px;top:70px;font:400 11px 'Poppins',sans-serif;color:var(--gold);letter-spacing:.6px}
.main-nav{position:absolute;left:487px;top:49px;display:flex;gap:30px;font:700 13px 'Roboto',Arial,sans-serif;color:var(--ink)}
.main-nav .active{color:var(--gold)}
.nav-caret{position:absolute;left:498px;top:90px;width:0;height:0;border-left:9px solid transparent;border-right:9px solid transparent;border-bottom:16px solid var(--black)}
.lang{position:absolute;left:1004px;top:40px;display:flex;align-items:center;gap:8px;font:700 12px 'Roboto',sans-serif;color:var(--gold)}
.lang .flag{width:34px;height:34px;border-radius:50%;background:linear-gradient(#c63b3f 0 50%,#e7e7ee 50%);position:relative;overflow:hidden}
.lang .flag::before{content:"";position:absolute;left:0;top:0;width:16px;height:17px;background:#2f3f86}

/* hero */
.hero{position:absolute;left:0;top:106px;width:1200px;height:714px}
.hero-title{left:112px;top:218px;font-size:44px;line-height:52px}
.hero-arrow{position:absolute;width:48px;height:48px;border-radius:50%;background:rgba(20,20,20,.7);display:flex;align-items:center;justify-content:center}

/* focus */
.focus{position:absolute;left:0;top:820px;width:1200px;height:1390px;background:var(--paper)}
.section-title{position:absolute;left:0;width:1200px;text-align:center;font-size:44px}
.topic-photo{position:absolute;width:473px;height:330px;border-radius:4px}
.topic-icon{position:absolute;width:84px;height:84px;border-radius:50%;background:var(--gold);border:4px solid var(--paper);display:flex;align-items:center;justify-content:center}
.topic-title{position:absolute;font-size:31px;line-height:36px}
.topic-copy{position:absolute;width:446px}

/* about & portfolio */
.about-title{left:111px;top:2310px;font-size:44px;line-height:52px}
.about-rule{position:absolute;left:598px;top:2318px;width:2px;height:181px;background:#888}
.portfolio-title{left:111px;top:2596px;font-size:44px;line-height:52px}
.tile{position:absolute}
.tile-frame{position:absolute;background:var(--gold)}

/* contact */
.contact{position:absolute;left:0;top:3000px;width:1200px;height:700px}
.contact-title{position:absolute;left:0;top:3180px;width:1200px;text-align:center;font:700 39px 'Poppins',sans-serif;color:var(--white)}
.field{position:absolute;background:var(--white);font:400 13.5px 'Roboto',sans-serif;color:#777;padding:16px 18px}
.submit{position:absolute;background:var(--black);color:var(--white);font:700 13.5px 'Roboto',sans-serif;display:flex;align-items:center;justify-content:center}
.info-icon{position:absolute;width:68px;height:68px;border-radius:50%;border:2px solid var(--white);display:flex;align-items:center;justify-content:center}
.info-text{position:absolute;color:var(--white);font:400 11.5px/19px 'Roboto',sans-serif}
.info-text b{display:block;font:400 14px/22px 'Roboto',sans-serif}

/* footer */
.site-footer{position:absolute;left:0;top:3700px;width:1200px;height:431px;background:var(--black);color:var(--white);font-family:'Poppins',sans-serif}
.foot-head{position:absolute;top:100px;font:600 15px 'Poppins',sans-serif}
.foot-list{position:absolute;top:135px;list-style:none;font:400 13.5px/28.3px 'Poppins',sans-serif}
.social{display:flex;gap:6px}
.social span{width:29px;height:29px;border-radius:50%;background:var(--white)}
.newsletter{position:absolute;left:805px;top:188px;width:284px;height:50px;border-radius:25px;background:var(--white);color:#777;font:400 12.5px 'Poppins',sans-serif;padding:16px 18px}
.newsletter .send{position:absolute;right:4px;top:4px;width:42px;height:42px;border-radius:50%;background:var(--gold);display:flex;align-items:center;justify-content:center}
.copyright{position:absolute;left:0;top:370px;width:1200px;text-align:center;font:400 13px 'Poppins',sans-serif}
</style>
</head>
<body>

<header class="site-header">
  <span class="brand-mark"></span>
  <div class="brand">Velden Consulting</div>
  <div class="tagline">clarity in motion</div>
  <nav class="main-nav">
    <span class="active">HOME</span><span>DETAIL</span><span>PORTFOLIO</span><span>CONTACT US</span><span>ABOUT US</span>
  </nav>
  <span class="nav-caret"></span>
  <div class="lang"><span class="flag" role="img" aria-label="English language flag"></span>ENG ˅</div>
</header>

<section class="hero">
  <div class="abs" role="img" aria-label="Two businessmen smiling while reviewing a tablet in a bright office" style="left:0;top:0;width:1200px;height:714px;background:linear-gradient(110deg,#d7dbe0 0%,#9aa4b4 35%,#4c5872 60%,#c8cbd2 85%,#e9e7e3 100%)"></div>
  <svg class="abs" style="left:0;top:0" width="1200" height="714" viewBox="0 0 1200 714">
    <polygon points="0,546 316,690 1200,540 1200,714 0,714" fill="var(--gold)"/>
    <polygon points="0,570 316,714 1200,558 1200,714 0,714" fill="var(--paper)"/>
  </svg>
  <h1 class="abs serif hero-title">Velden Consulting<br>Supports</h1>
  <div class="btn" style="left:112px;top:334px;width:156px;height:54px">GET STARTED</div>
  <div class="hero-arrow" style="left:31px;top:273px"><svg width="14" height="14" viewBox="0 0 14 14"><path d="M9 2 4 7l5 5" stroke="#fff" stroke-width="2" fill="none"/></svg></div>
  <div class="hero-arrow" style="left:1118px;top:273px"><svg width="14" height="14" viewBox="0 0 14 14"><path d="M5 2l5 5-5 5" stroke="#fff" stroke-width="2" fill="none"/></svg></div>
  <svg class="abs" style="left:746px;top:287px" width="112" height="112" viewBox="0 0 112 112">
    <circle cx="56" cy="56" r="55" fill="rgba(255,255,255,.35)"/>
    <circle cx="56" cy="56" r="42" fill="#fff"/>
    <polygon points="46,38 76,56 46,74" fill="var(--gold)"/>
  </svg>
</section>

<section class="focus">
  <h2 class="serif section-title" style="top:92px">Our Focus Topics</h2>
</section>

<!-- topic 1 -->
<div class="topic-photo" role="img" aria-label="Team meeting around a conference table in a modern office" style="left:111px;top:995px;background:linear-gradient(120deg,#e3e4e4,#8d8f93 50%,#cfd0cf)"></div>
<div class="topic-icon" style="left:539px;top:1116px"><svg width="44" height="44" viewBox="0 0 44 44" fill="none" stroke="#fff" stroke-width="2"><rect x="5" y="7" width="34" height="24"/><path d="M10 26l7-8 6 5 8-10M16 31l-4 8M28 31l4 8"/></svg></div>
<h3 class="serif topic-title" style="left:640px;top:988px">IT Strategy Consulting</h3>
<p class="copy topic-copy" style="left:640px;top:1035px">Lorem ipsum dolor sit amet, consectetur adipiscing elit, sed do eiusmod tempor incididunt ut labore et dolore magna aliqua. Ut enim ad minim veniam, quis nostrud exercitation ullamco laboris nisi ut aliquip ex ea commodo consequat. Duis aute irure dolor in reprehenderit in voluptate velit esse cillum dolore eu fugiat nulla pariatur. Excepteur sint occaecat cupidatat non proident, sunt in culpa qui officia deserunt mollit anim id est laborum.Lorem ipsum dolor sit amet, consectetur adipiscing elit, sed do eiusmod tempor incididunt ut labore et dolore magna aliqua. Ut enim ad minim veniam, quis nostrud exercitation ullamco laboris nisi ut aliquip ex ea commodo consequat. Duis aute irure</p>
<div class="btn" style="left:640px;top:1277px;width:131px;height:45px">LEARN MORE</div>

<!-- topic 2 -->
<h3 class="serif topic-title" style="left:111px;top:1382px">Digital Transformation</h3>
<p class="copy topic-copy" style="left:111px;top:1432px">Lorem ipsum dolor sit amet, consectetur adipiscing elit, sed do eiusmod tempor incididunt ut labore et dolore magna aliqua. Ut enim ad minim veniam, quis nostrud exercitation ullamco laboris nisi ut aliquip ex ea commodo consequat. Duis aute irure dolor in reprehenderit in voluptate velit esse cillum dolore eu fugiat nulla pariatur. Excepteur sint occaecat cupidatat non proident, sunt in culpa qui officia deserunt mollit anim id est laborum.Lorem ipsum dolor sit amet, consectetur adipiscing elit, sed do eiusmod tempor incididunt ut labore et dolore magna aliqua. Ut enim ad minim veniam, quis nostrud exercitation ullamco laboris nisi ut aliquip ex ea commodo consequat. Duis aute irure</p>
<div class="btn" style="left:111px;top:1670px;width:131px;height:45px">LEARN MORE</div>
<div class="topic-photo" role="img" aria-label="Colleagues discussing work at laptops in an office" style="left:616px;top:1389px;background:linear-gradient(120deg,#c9cbcf,#5f6f8a 45%,#d4d6d9)"></div>
<div class="topic-icon" style="left:574px;top:1511px"><svg width="44" height="44" viewBox="0 0 44 44" fill="none" stroke="#fff" stroke-width="2"><circle cx="22" cy="17" r="9"/><path d="M18 28h8v6h-8zM22 3v3M8 17H5M39 17h-3M11 7l2 2M33 7l-2 2"/></svg></div>

<!-- topic 3 -->
<div class="topic-photo" role="img" aria-label="Two colleagues reviewing documents and a tablet" style="left:111px;top:1784px;background:linear-gradient(120deg,#e2e2df,#3c4a68 45%,#d9c9a8 70%,#e6e6e4)"></div>
<div class="topic-icon" style="left:539px;top:1904px"><svg width="44" height="44" viewBox="0 0 44 44" fill="none" stroke="#fff" stroke-width="2"><circle cx="22" cy="18" r="12"/><path d="M16 18l4 4 8-8M15 29l-3 11 6-3 4 4M29 29l3 11-6-3"/></svg></div>
<h3 class="serif topic-title" style="left:640px;top:1776px">IT Quality Management</h3>
<p class="copy topic-copy" style="left:640px;top:1824px">Lorem ipsum dolor sit amet, consectetur adipiscing elit, sed do eiusmod tempor incididunt ut labore et dolore magna aliqua. Ut enim ad minim veniam, quis nostrud exercitation ullamco laboris nisi ut aliquip ex ea commodo consequat. Duis aute irure dolor in reprehenderit in voluptate velit esse cillum dolore eu fugiat nulla pariatur. Excepteur sint occaecat cupidatat non proident, sunt in culpa qui officia deserunt mollit anim id est laborum.Lorem ipsum dolor sit amet, consectetur adipiscing elit, sed do eiusmod tempor incididunt ut labore et dolore magna aliqua. Ut enim ad minim veniam, quis nostrud exercitation ullamco laboris nisi ut aliquip ex ea commodo consequat. Duis aute irure</p>
<div class="btn" style="left:640px;top:2066px;width:131px;height:45px">LEARN MORE</div>

<!-- about -->
<h2 class="abs serif about-title">About<br>Velden Consulting</h2>
<span class="about-rule"></span>
<p class="abs copy" style="left:624px;top:2314px;width:466px">Lorem ipsum dolor sit amet, consectetur adipiscing elit, sed do eiusmod tempor incididunt ut labore et dolore magna aliqua. Ut enim ad minim veniam, quis nostrud exercitation ullamco laboris nisi ut aliquip ex ea commodo consequat. Duis aute irure dolor in reprehenderit in voluptate velit esse cillum dolore eu fugiat nulla pariatur. Excepteur sint occaecat cupidatat non proident, sunt in culpa qui officia deserunt mollit anim id est laborum.</p>
<div class="btn" style="left:624px;top:2456px;width:130px;height:45px">LEARN MORE</div>

<!-- portfolio -->
<h2 class="abs serif portfolio-title">Our Portfolio</h2>
<p class="abs copy" style="left:111px;top:2656px;width:450px">Our range of services covers the management of the entire development process from applications and extensions to quality assurance through to going live and support afterwards.</p>
<p class="abs copy" style="left:111px;top:2741px;width:450px">Velden Consulting specializes in complex projects in heterogeneous IT environments. We deliver in high quality. We deliver with the necessary procedural models to achieve customer satisfaction and project success. We bring a reasonable degree of pragmatism and approach things optimistically without losing sight of reality. We master difficult situations.</p>
<div class="btn" style="left:111px;top:2865px;width:131px;height:45px">LEARN MORE</div>

<div class="tile-frame" style="left:795px;top:2613px;width:117px;height:100px"></div>
<div class="tile" role="img" aria-label="Portrait of a consultant with glasses" style="left:786px;top:2603px;width:117px;height:100px;background:linear-gradient(#dfe1e3,#8b8f95)"></div>
<div class="tile-frame" style="left:692px;top:2708px;width:103px;height:117px"></div>
<div class="tile" role="img" aria-label="Hands pointing at a document during a meeting" style="left:683px;top:2698px;width:103px;height:117px;background:linear-gradient(120deg,#c9cdd3,#6e7c95)"></div>
<div class="tile-frame" style="left:914px;top:2708px;width:102px;height:117px"></div>
<div class="tile" role="img" aria-label="Business people in discussion" style="left:905px;top:2698px;width:102px;height:117px;background:linear-gradient(120deg,#d8dadc,#9aa0a8)"></div>
<div class="tile-frame" style="left:795px;top:2825px;width:117px;height:96px"></div>
<div class="tile" role="img" aria-label="Person working at a laptop" style="left:786px;top:2815px;width:117px;height:96px;background:linear-gradient(#b9bdc2,#e1e2e3)"></div>
<div class="tile-frame" style="left:790px;top:2703px;width:113px;height:112px"></div>
<div class="tile" style="left:795px;top:2708px;width:103px;height:102px;background:var(--white)"></div>

<!-- contact -->
<section class="contact">
  <svg class="abs" style="left:0;top:0" width="1200" height="700" viewBox="0 0 1200 700">
    <defs><linearGradient id="goldfade" x1="0" y1="0" x2="1" y2="1"><stop offset="0" stop-color="#b47a05"/><stop offset="1" stop-color="#c68a0c"/></linearGradient></defs>
    <polygon points="0,181 882,16 1200,181 1200,700 0,700" fill="url(#goldfade)"/>
    <polygon points="0,178 882,10 882,17 0,182" fill="var(--black)"/>
    <polygon points="882,10 1200,170 1200,192 882,30 870,12" fill="var(--black)"/>
  </svg>
</section>
<h2 class="contact-title">CONTACT US</h2>
<div class="field" style="left:294px;top:3256px;width:296px;height:45px">Name</div>
<div class="field" style="left:294px;top:3317px;width:296px;height:45px">Phone</div>
<div class="field" style="left:294px;top:3378px;width:296px;height:45px">Email address</div>
<div class="field" style="left:294px;top:3439px;width:296px;height:45px">Email address</div>
<div class="field" style="left:610px;top:3256px;width:296px;height:167px">Message</div>
<div class="submit" style="left:610px;top:3439px;width:296px;height:45px">SUBMIT</div>

<div class="info-icon" style="left:211px;top:3528px"><svg width="22" height="26" viewBox="0 0 22 26"><path d="M11 1a9 9 0 0 0-9 9c0 7 9 15 9 15s9-8 9-15a9 9 0 0 0-9-9z" fill="#fff"/><circle cx="11" cy="10" r="3.5" fill="var(--gold)"/></svg></div>
<div class="info-text" style="left:300px;top:3526px"><b>ADDRESS :</b>Velden Consulting GmbH<br>Parkstraße 12 - 14<br>D-80331 Lindenau</div>
<div class="info-icon" style="left:487px;top:3528px"><svg width="24" height="24" viewBox="0 0 24 24"><path d="M6 2l4 5-2 3c1 3 3 5 6 6l3-2 5 4-2 4c-9 0-18-9-18-18z" fill="#fff"/></svg></div>
<div class="info-text" style="left:576px;top:3526px"><b>PHONE :</b>Phone: +49 (0) 8000 1234560<br>Fax: +49 (0) 8000 1234561</div>
<div class="info-icon" style="left:755px;top:3528px"><svg width="26" height="20" viewBox="0 0 26 20"><rect x="1" y="1" width="24" height="18" rx="2" fill="#fff"/><path d="M2 3l11 8 11-8" stroke="var(--gold)" stroke-width="2" fill="none"/></svg></div>
<div class="info-text" style="left:844px;top:3526px"><b>EMAIL:</b>info (at) vldn-consult.example<br>http://www.vldn-consult.example</div>

<footer class="site-footer">
  <div class="foot-head" style="left:111px">NAVIGATION</div>
  <ul class="foot-list" style="left:111px"><li>Home</li><li>About us</li><li>Services</li><li>Solution</li><li>Support</li><li>Insights</li></ul>
  <div class="foot-head" style="left:318px">OUR SERVICES</div>
  <ul class="foot-list" style="left:318px"><li>Sit voluptatem</li><li>Accusantium</li><li>Doloremque</li><li>Sit voluptatem</li><li>Accusantium</li><li>Doloremque</li></ul>
  <div class="foot-head" style="left:547px">CONTACT US</div>
  <ul class="foot-list" style="left:547px">
    <li>&#9990;&nbsp; +1 888 888 8888</li>
    <li style="padding-left:21px;text-indent:-21px">&#9679;&nbsp;&nbsp; 123,Lorem ipsum dolor sit<br>amet, consectetur</li>
  </ul>
  <div class="foot-head" style="left:547px;top:237px">FOLLOW US</div>
  <div class="abs social" style="left:547px;top:270px"><span></span><span></span><span></span><span></span></div>
  <div class="foot-head" style="left:810px;top:98px">RECEIVE OUR NEWSLETTER</div>
  <p class="abs" style="left:810px;top:130px;width:290px;font:400 13px/28px 'Poppins',sans-serif">Sign up today to get resources on how to attract and retain more customers!</p>
  <div class="newsletter">Email Address<span class="send"><svg width="18" height="18" viewBox="0 0 18 18"><path d="M1 9 17 1 13 17 9 11z" fill="#fff"/></svg></span></div>
  <div class="copyright">Copyright © 2021. All Rights Reserved</div>
</footer>

</body>
</html>
```